New letter head for Air Conditioning business

We need a new professional letter head design to suit our new re-branded air conditioning business. Our new logo is attached

```html
<!DOCTYPE html>
<html lang="en">
<head>
<meta charset="utf-8">
<title>Corvane Letterhead</title>
<link href="https://fonts.googleapis.com/css2?family=Poppins:wght@400;500;600;700&display=swap" rel="stylesheet">
<style>
  :root {
    --green: #67c187;
    --green-deep: #4aa96f;
    --ink: #111111;
    --charcoal: #3a3a3c;
    --paper-edge: #ebe7e8;
    --paper-mid: #fbfbfb;
    --backdrop: #dcdce3;
    --accent-red: #e8604c;
  }
  * { margin: 0; padding: 0; box-sizing: border-box; }
  html, body { width: 1200px; height: 1200px; overflow: hidden; }
  body {
    background: var(--backdrop);
    font-family: "Poppins", sans-serif;
    color: var(--ink);
    position: relative;
  }
  .letterhead {
    position: absolute;
    left: 176px; top: 0;
    width: 848px; height: 1200px;
    background: linear-gradient(180deg, var(--paper-edge) 0%, var(--paper-mid) 38%, var(--paper-mid) 55%, var(--paper-edge) 100%);
    overflow: hidden;
  }
  .top-band { position: absolute; left: 0; top: 0; width: 100%; height: 22px; background: var(--green); }

  .brand { position: absolute; left: 44px; top: 76px; display: flex; align-items: center; gap: 14px; }
  .brand-mark { width: 40px; height: 40px; border-radius: 50%; background: var(--green); }
  .brand-name { font-size: 34px; font-weight: 600; letter-spacing: 3px; color: var(--charcoal); }

  .contact-list { position: absolute; left: 568px; top: 62px; list-style: none; }
  .contact-item { display: flex; align-items: center; height: 27px; margin-bottom: 12px; font-size: 14px; font-weight: 500; }
  .contact-icon { width: 27px; height: 27px; border-radius: 50%; background: var(--green); display: flex; align-items: center; justify-content: center; margin-right: 22px; flex: none; }
  .contact-icon svg { width: 15px; height: 15px; }
  .contact-item.web .contact-icon { background: none; }
  .contact-item.web .contact-icon svg { width: 25px; height: 25px; }

  .recipient-name { position: absolute; left: 60px; top: 316px; font-size: 21px; font-weight: 600; }
  .recipient-address { position: absolute; left: 60px; top: 356px; font-size: 21px; font-weight: 500; }
  .letter-date { position: absolute; right: 54px; top: 316px; font-size: 21px; font-weight: 600; }

  .letter-body { position: absolute; left: 55px; right: 54px; top: 414px; font-size: 17px; line-height: 19.9px; text-align: justify; }
  .letter-body p + p { margin-top: 28px; }

  .sign-off { position: absolute; left: 60px; top: 780px; font-size: 20px; font-weight: 500; }
  .signature { position: absolute; left: 54px; top: 838px; width: 180px; height: 62px; background: linear-gradient(90deg, #e4e2e4, #f4f3f4); border-radius: 4px; }
  .sender-name { position: absolute; left: 54px; top: 932px; font-size: 19.5px; font-weight: 500; }
  .sender-title { position: absolute; left: 54px; top: 969px; font-size: 19.5px; font-weight: 500; }

  .footer-art { position: absolute; left: 0; bottom: 0; width: 848px; height: 48px; }
</style>
</head>
<body>
  <main class="letterhead">
    <div class="top-band"></div>

    <div class="brand">
      <span class="brand-mark"></span>
      <span class="brand-name">CORVANE</span>
    </div>

    <ul class="contact-list">
      <li class="contact-item phone">
        <span class="contact-icon">
          <svg viewBox="0 0 24 24"><path fill="#fff" d="M6.6 10.8a15 15 0 0 0 6.6 6.6l2.2-2.2c.3-.3.7-.4 1-.2 1.1.4 2.3.6 3.6.6.6 0 1 .4 1 1V20c0 .6-.4 1-1 1A17 17 0 0 1 3 4c0-.6.4-1 1-1h3.5c.6 0 1 .4 1 1 0 1.3.2 2.5.6 3.6.1.3 0 .7-.2 1z"/></svg>
        </span>
        +12345689
      </li>
      <li class="contact-item web">
        <span class="contact-icon">
          <svg viewBox="0 0 24 24" fill="none" stroke="#67c187" stroke-width="1.6"><circle cx="12" cy="12" r="9"/><ellipse cx="12" cy="12" rx="4" ry="9"/><path d="M3 12h18M4.5 7.5h15M4.5 16.5h15"/></svg>
        </span>
        www.yourwebsite.com
      </li>
      <li class="contact-item mail">
        <span class="contact-icon">
          <svg viewBox="0 0 24 24" fill="none" stroke="#fff" stroke-width="1.8"><rect x="3" y="6" width="18" height="12" rx="1"/><path d="M3 6l9 7 9-7"/></svg>
        </span>
        yourgmail@.com
      </li>
    </ul>

    <h2 class="recipient-name">Your&nbsp; Name Here</h2>
    <p class="recipient-address">Address</p>
    <p class="letter-date">Date : 4.6.2021</p>

    <section class="letter-body">
      <p>Lorem ipsum dolor sit amet, consectetur adipiscing elit. Nam pretium quam eget feugiat tincidunt. Nullam consequat mi vitae pharetra sagittis. Suspendisse porta placerat velit, ac condimentum felis molestie in. Nullam eget velit in erat consectetur semper vitae ac nisi. Donec et lectus ut purus aliquam pulvinar non in arcu. Vestibulum et turpis a nisl placerat euismod. Aliquam eu quam augue. Cras consectetur, velit ut semper aliquam, odio tortor suscipit nulla, et vulputate dui risus at ante. Maecenas ac dignissim ex. Pellentesque in dignissim massa. Fusce at posuere lorem. Vivamus molestie nisl ac nisi rhoncus vulputate. Aenean augue arcu, maximus ut consequat in, lobortis sit amet lectus. Suspendisse dapibus auctor quam, sed tempor orci euismod accumsan. In hac habitasse platea dictumst. Suspendisse ut enim metus.</p>
      <p>Nullam at mi eros. Lorem ipsum dolor sit amet, consectetur adipiscing elit. Vestibulum tempus, sem id pharetra ultrices, magna nulla aliquet sapien, ac fringilla odio tortor in eros. Duis a urna sem. Nunc ac purus mattis, pharetra urna quis, ultrices quam. Proin ac sollicitudin dolor, ac feugiat turpis. Sed aliquet ornare nisi, vitae finibus tortor vehicula auctor.</p>
    </section>

    <p class="sign-off">Regards</p>
    <div class="signature" role="img" aria-label="Handwritten signature of the sender"></div>
    <p class="sender-name">Your Name Here</p>
    <p class="sender-title">Designation Here</p>

    <svg class="footer-art" viewBox="0 0 848 48" preserveAspectRatio="none">
      <defs>
        <linearGradient id="footerGreen" x1="0" y1="0" x2="0" y2="1">
          <stop offset="0" stop-color="#4aa96f"/>
          <stop offset="1" stop-color="#67c187"/>
        </linearGradient>
      </defs>
      <polygon points="0,0 236,0 212,48 0,48" fill="url(#footerGreen)"/>
      <rect x="271" y="23" width="577" height="3.5" fill="#4a4a4c"/>
      <rect x="212" y="41" width="636" height="7" fill="#67c187"/>
    </svg>
  </main>
</body>
</html>
```